Velmora Systems Website

Website design for our company: Velmora Systems.
The website should look fresh and IT focused. Please have a look at http://www.velmorasystems.example.au/ for our current design. We want something fresh and new, professional looking, in WordPress so we can easily make changes.

It Company

```html
<!DOCTYPE html>
<html lang="en">
<head>
<meta charset="utf-8">
<title>Velmora Systems</title>
<link rel="stylesheet" href="https://fonts.googleapis.com/css2?family=Open+Sans:wght@400;600;700&family=Arimo:ital,wght@0,400;0,700;1,400&display=swap">
<style>
:root{
  --blue:#0b72c4;
  --blue-dark:#0a5fa6;
  --green:#0aa74b;
  --green-dark:#08913f;
  --grey:#666666;
  --ink:#333333;
  --white:#ffffff;
  --sky1:#5d9fd8;
  --sky2:#cfe3f3;
}
*{margin:0;padding:0;box-sizing:border-box}
html,body{width:952px;height:1200px;overflow:hidden;background:#fff}
body{position:relative;font-family:Arimo,Arial,sans-serif;color:var(--ink)}
.abs{position:absolute}
.heading{font-family:"Open Sans",Arial,sans-serif;font-weight:600}

/* header */
.site-header{left:0;top:0;width:952px;height:93px;background:linear-gradient(#fff,#f2f2f2);border-top:2px solid var(--blue);border-bottom:1px solid #ddd}
.brand{left:140px;top:17px;width:121px;height:60px;background:var(--green);border:3px solid #fff;box-shadow:0 0 0 1px #bbb;display:flex;align-items:center;justify-content:center;gap:5px;color:#fff;font-family:"Open Sans",Arial,sans-serif;font-weight:600;font-size:12px;border-radius:3px}
.brand .dot{width:14px;height:14px;border-radius:50%;background:#fff}
.search{left:520px;top:26px;width:147px;height:22px;border:1px solid #ccc;background:#fff;font-style:italic;font-size:10px;color:#777;padding:5px 6px}
.search svg{position:absolute;right:5px;top:4px}
.call{left:688px;top:22px}
.call small{position:absolute;left:30px;top:0;font-size:10px;white-space:nowrap;font-family:"Open Sans",Arial,sans-serif}
.call strong{position:absolute;left:30px;top:11px;font-size:16px;font-weight:400;white-space:nowrap;font-family:"Open Sans",Arial,sans-serif}
.main-nav{left:315px;top:63px;display:flex;font-family:"Open Sans",Arial,sans-serif;font-size:11px;font-weight:600;color:#333}
.main-nav a{padding:0 12px;border-left:1px solid #bbb;line-height:14px;color:inherit;text-decoration:none}
.main-nav a:first-child{border-left:0;color:var(--green)}

/* hero */
.hero{left:0;top:93px;width:952px;height:334px;background:linear-gradient(#9cc6ec 0%,var(--sky2) 55%,#e8eef2 85%,#8fae5a 100%)}
.hero-caption{left:0;top:391px;width:952px;height:36px;background:rgba(11,114,196,.75);color:#fff;text-align:center;font-family:"Open Sans",Arial,sans-serif;font-size:19px;line-height:36px}
.hero-arrow{top:231px;width:34px;height:34px;border-radius:50%;background:#333;border:3px solid #888;box-shadow:0 2px 4px rgba(0,0,0,.5)}

/* services */
.services{left:0;top:427px;width:952px;height:257px;background:var(--blue)}
.sec-title{font-size:17px;color:#fff}
.dash{height:0;border-top:1px dashed rgba(255,255,255,.7)}
.service{width:130px;text-align:center;color:#fff}
.service h3{font-family:"Open Sans",Arial,sans-serif;font-weight:600;font-size:11.5px;height:22px}
.service .disc{width:94px;height:94px;border-radius:50%;background:radial-gradient(#fafafa,#dcdcdc);border:4px solid #fff;margin:6px auto 0;display:flex;align-items:center;justify-content:center;box-shadow:0 6px 6px rgba(0,0,0,.2)}
.service .disc.on{background:var(--green)}
.service p{font-size:10px;line-height:14px;margin-top:18px}

/* info band */
.info{left:0;top:684px;width:952px;height:276px;background:var(--grey);color:#fff}
.info h2{font-size:17px}
.info .rule{border-top:1px dashed #aaa}
.photo{left:141px;top:745px;width:203px;height:93px;border:1px solid #fff;background:linear-gradient(90deg,#8a8f96,#c9cdd2 45%,#3b3f46)}
.about-text{left:141px;top:844px;width:203px;font-size:8.6px;line-height:12.6px;text-align:justify}
.more{font-size:9px;font-weight:700}
.quote{font-size:9.3px;line-height:14.5px}
.cite{font-size:8.3px;font-weight:700;text-align:right}
.field{background:#fff;border:1px solid #ccc;font-style:italic;font-size:9px;color:#888;padding:4px 8px;width:203px}
.btn{background:var(--green);color:#fff;font-family:"Open Sans",Arial,sans-serif;font-weight:600;font-size:11px;padding:2px 7px}

/* clients */
.clients-title{font-size:17px;color:var(--blue)}
.rule-grey{border-top:1px dashed #999}
.client{top:1024px;font-family:"Open Sans",Arial,sans-serif;font-weight:700;font-size:19px;color:#555}

/* footer */
.footer{left:0;top:1085px;width:952px;height:115px;background:var(--green);color:#fff}
.fbox{top:14px;height:57px;border:1px solid rgba(255,255,255,.35);background:var(--green-dark);padding:7px 9px}
.fbox h4{font-family:"Open Sans",Arial,sans-serif;font-weight:600;font-size:11px}
.fbox p{font-size:9px;margin-top:4px;display:flex;align-items:center;gap:6px}
.social{width:18px;height:18px;border-radius:3px}
.foot-links{left:140px;top:92px;font-size:9px}
.copy{left:610px;top:92px;font-size:9px}
</style>
</head>
<body>

<header class="site-header abs">
  <div class="brand abs"><span class="dot"></span>Velmora Systems</div>
  <div class="search abs">search
    <svg width="12" height="12" viewBox="0 0 12 12"><circle cx="5" cy="5" r="3.5" fill="none" stroke="#888" stroke-width="1.5"/><path d="M7.5 7.5 11 11" stroke="#888" stroke-width="1.8"/></svg>
  </div>
  <div class="call abs">
    <svg width="24" height="24" viewBox="0 0 24 24"><circle cx="12" cy="12" r="11" fill="none" stroke="var(--green)" stroke-width="1.5"/><path d="M8 6c-2 2-1 6 2 9s6 4 8 2l-2-2-2 1c-1-.5-3-2.5-3.5-3.5l1-2z" fill="var(--green)"/></svg>
    <small>Call Us Today</small><strong>123 456 7890</strong>
  </div>
  <nav class="main-nav abs">
    <a href="#">HOME</a><a href="#">ABOUT US</a><a href="#">SERVICES</a><a href="#">SUPPORT</a><a href="#">TESTIMONIALS</a><a href="#">CLIENTS</a><a href="#">CONTACT US</a>
  </nav>
</header>

<section class="hero abs" role="img" aria-label="Man relaxing outdoors with a laptop under a blue sky"></section>
<div class="hero-arrow abs" style="left:141px"><svg width="28" height="28" viewBox="0 0 28 28"><path d="M16 8l-6 6 6 6" fill="none" stroke="#fff" stroke-width="2"/></svg></div>
<div class="hero-arrow abs" style="left:777px"><svg width="28" height="28" viewBox="0 0 28 28"><path d="M12 8l6 6-6 6" fill="none" stroke="#fff" stroke-width="2"/></svg></div>
<div class="hero-caption abs">WE HAVE SPECIALISED ENGINEERS, TRAINED TO DO SPECIALISED WORK</div>

<section class="services abs">
  <h2 class="sec-title heading abs" style="left:143px;top:28px">Our Services</h2>
  <svg class="abs" style="left:780px;top:36px" width="32" height="12" viewBox="0 0 32 12"><path d="M7 1 2 6l5 5M24 1l5 5-5 5" fill="none" stroke="#fff" stroke-width="1.3"/></svg>
  <div class="dash abs" style="left:142px;top:50px;width:672px"></div>

  <div class="service abs" style="left:133px;top:72px"><h3>On-site Service</h3>
    <div class="disc on"><svg width="50" height="50" viewBox="0 0 50 50"><path d="M12 38 34 16M16 12l22 22" stroke="#fff" stroke-width="6" stroke-linecap="round"/><circle cx="36" cy="13" r="6" fill="#fff"/></svg></div>
    <p>Lorem ipsum dolor sit amet<br>ummy nibh eui smod</p></div>
  <div class="service abs" style="left:271px;top:72px"><h3>Remote Desktop</h3>
    <div class="disc"><svg width="50" height="50" viewBox="0 0 50 50" fill="none" stroke="#555" stroke-width="3"><rect x="6" y="8" width="28" height="20"/><path d="M14 34h12"/><circle cx="34" cy="32" r="10" fill="#eee"/><path d="M30 30l8 0m-8 4h8" stroke-width="2"/></svg></div>
    <p>Lorem ipsum dolor sit amet<br>ummy nibh eui smod</p></div>
  <div class="service abs" style="left:410px;top:72px"><h3>Medical IT Service</h3>
    <div class="disc"><svg width="50" height="50" viewBox="0 0 50 50" fill="none" stroke="#555" stroke-width="3"><path d="M8 8v12a8 8 0 0 0 16 0V8M16 28v6a8 8 0 0 0 16 0v-6"/><circle cx="36" cy="14" r="5"/><circle cx="32" cy="26" r="3"/></svg></div>
    <p>Lorem ipsum dolor sit amet<br>ummy nibh eui smod</p></div>
  <div class="service abs" style="left:548px;top:72px"><h3>Pharmacy IT</h3>
    <div class="disc"><svg width="50" height="50" viewBox="0 0 50 50" fill="none" stroke="#555" stroke-width="3"><rect x="6" y="8" width="32" height="24"/><path d="M10 26l7-8 6 5 9-10"/><circle cx="36" cy="34" r="6" fill="#eee"/><path d="M40 38l5 5"/></svg></div>
    <p>Lorem ipsum dolor sit amet<br>ummy nibh eui smod</p></div>
  <div class="service abs" style="left:687px;top:72px"><h3>Website Design</h3>
    <div class="disc"><svg width="50" height="50" viewBox="0 0 50 50" fill="none" stroke="#555" stroke-width="3"><rect x="6" y="12" width="36" height="24"/><path d="M18 42h12M24 36v6M22 28l14-18"/></svg></div>
    <p>Lorem ipsum dolor sit amet<br>ummy nibh eui smod</p></div>
</section>

<section class="info abs">
  <h2 class="heading abs" style="left:141px;top:28px">About Velmora Systems</h2>
  <div class="rule abs" style="left:141px;top:52px;width:203px"></div>
  <h2 class="heading abs" style="left:373px;top:28px">Client Testimonials</h2>
  <div class="rule abs" style="left:373px;top:52px;width:203px"></div>
  <h2 class="heading abs" style="left:608px;top:28px">Quick Contact</h2>
  <div class="rule abs" style="left:608px;top:52px;width:204px"></div>

  <p class="quote abs" style="left:373px;top:65px;width:210px">“ Nonummy nibh uismod tincidunt ut laoreet dolore magna aliquam erat volutpat. Ut wisi enim ad minim nonummy nibh euismod tincidunt ”</p>
  <p class="cite abs" style="left:373px;top:110px;width:204px">Dana Rowell-QRS</p>
  <p class="quote abs" style="left:373px;top:128px;width:210px">“ I have always found the team extremely helpful with their advice over the phone. They also have the ability to access our computers remotely, and can rectify most problems quite swiftly. I have no hesitation in recommending Velmora Systems for all of your IT needs. ”</p>
  <p class="cite abs" style="left:373px;top:215px;width:207px">Marcus Delaine B.Pharm<br>Northfield Care Chemists, Greenvale</p>
  <p class="more abs" style="left:529px;top:240px">Read More »</p>

  <div class="field abs" style="left:609px;top:62px">Name</div>
  <div class="field abs" style="left:609px;top:95px">Email</div>
  <div class="field abs" style="left:609px;top:127px">Phone</div>
  <div class="field abs" style="left:609px;top:159px;height:60px">Message</div>
  <div class="btn abs" style="left:610px;top:230px">Submit</div>
</section>
<div class="photo abs" role="img" aria-label="Team of colleagues meeting around a table"></div>
<p class="about-text abs" style="color:#fff">Velmora Systems is an Adelaide based company with a single objective - to excel in the support and service of all computer and IT needs. We provide a high level of consulting services using the most experienced engineers at a reasonable and fair price. We believe in using a Business Value approach to every......</p>
<p class="more abs" style="left:288px;top:924px;color:#fff">Read More »</p>

<h2 class="clients-title heading abs" style="left:140px;top:978px">Our Clients</h2>
<svg class="abs" style="left:555px;top:985px" width="32" height="12" viewBox="0 0 32 12"><path d="M7 1 2 6l5 5M24 1l5 5-5 5" fill="none" stroke="var(--green)" stroke-width="1.3"/></svg>
<div class="rule-grey abs" style="left:140px;top:1003px;width:447px"></div>
<span class="client abs" style="left:142px">Corvane</span>
<span class="client abs" style="left:280px;font-weight:400;color:#888">nimbra</span>
<span class="client abs" style="left:422px">KESTO</span>
<span class="client abs" style="left:515px;color:#666">lumora</span>
<h2 class="clients-title heading abs" style="left:604px;top:980px">Remote Support</h2>
<div class="rule-grey abs" style="left:604px;top:1003px;width:207px"></div>
<div class="field abs" style="left:604px;top:1013px;width:202px">Enter your 6 digit code</div>
<div class="btn abs" style="left:605px;top:1040px">Connect Now</div>

<footer class="footer abs">
  <div class="fbox abs" style="left:140px;width:184px"><h4>Subscribe to Newsletter</h4>
    <div style="margin-top:6px;display:flex;gap:5px"><span style="background:#0a8a3c;width:132px;height:20px;font-style:italic;font-size:9px;padding:5px 7px">Email here</span><span style="background:#0a8a3c;width:24px;height:20px;display:flex;align-items:center;justify-content:center"><svg width="10" height="10" viewBox="0 0 10 10"><path d="M3 1l4 4-4 4" fill="none" stroke="#fff" stroke-width="2"/></svg></span></div></div>
  <div class="fbox abs" style="left:363px;width:162px"><h4>Contact Us</h4>
    <p><svg width="9" height="9" viewBox="0 0 10 10"><path d="M2 1c-2 2 0 5 3 7s4 1 4 0L7 6 6 7C5 6.5 3.5 5 3 4l1-1z" fill="#fff"/></svg>123 456 7890</p>
    <p style="margin-top:2px"><svg width="10" height="8" viewBox="0 0 10 8"><rect width="10" height="8" fill="#fff"/><path d="M0 0l5 4 5-4" stroke="#0a8a3c" fill="none"/></svg>support@velmorasystems.example.au</p></div>
  <div class="fbox abs" style="left:564px;width:88px"><h4>Follow Us</h4>
    <div style="display:flex;gap:10px;margin-top:8px"><span class="social" style="background:#3b5998"></span><span class="social" style="background:#4fb3e0"></span><span class="social" style="background:#f37021"></span></div></div>
  <div class="brand abs" style="left:692px;top:12px;width:119px;height:61px">
    <span class="dot"></span>Velmora Systems</div>
  <p class="foot-links abs">Home &nbsp;| &nbsp;About Us &nbsp;| &nbsp;Services | &nbsp;Support &nbsp;| &nbsp;Testimonials &nbsp;| &nbsp;Clients &nbsp;| &nbsp;Contact Us &nbsp;| &nbsp;Terms Conditions</p>
  <p class="copy abs">Copyright © 2014 &nbsp;velmorasystems. &nbsp;All Rights Reserved</p>
</footer>

</body>
</html>
```